Lo Mara Menu Design Project

This project is pretty straight forward. You will be given 3 files which include the following:
1. Our proposed menu
2. Our Company logo
3. A sample menu on what we are looking for design wise

Your job is to create a visually pleasing menu that is simple, clean and fresh. Please refer to our home website for additional information. (www.lomara-eats.com) Must be in eps or equivalent format.

Target Market(s)

20s to 40s

Industry/Entity Type

It Company

Requirements
Must have
• Company log
Must be in EPS format

```html
<!DOCTYPE html>
<html lang="en">
<head>
<meta charset="utf-8">
<title>Lo Mara Menu – Salads &amp; Chicken</title>
<link rel="stylesheet" href="https://fonts.googleapis.com/css2?family=Josefin+Sans:ital,wght@0,400;0,600;0,700;1,300;1,400&display=swap">
<style>
  :root {
    --bg-deep: #1c0d0b;
    --bg-warm: #3b1510;
    --bg-ember: #5a1c14;
    --accent-red: #c81f2a;
    --text-light: #f3ece8;
    --text-soft: #e2d8d3;
  }
  html, body {
    margin: 0;
    padding: 0;
    width: 1200px;
    height: 1000px;
    overflow: hidden;
    background: var(--bg-deep);
  }
  .menu-page {
    position: relative;
    width: 1200px;
    height: 1000px;
    overflow: hidden;
    font-family: "Josefin Sans", "Century Gothic", sans-serif;
    color: var(--text-light);
  }
  .food-backdrop {
    position: absolute;
    inset: 0;
    background:
      radial-gradient(ellipse at 30% 65%, rgba(120,36,22,0.55), transparent 55%),
      radial-gradient(ellipse at 80% 55%, rgba(95,40,20,0.5), transparent 50%),
      radial-gradient(ellipse at 55% 20%, rgba(60,70,30,0.35), transparent 45%),
      linear-gradient(180deg, var(--bg-warm) 0%, var(--bg-deep) 55%, #24110d 100%);
  }
  .salads-band {
    position: absolute;
    left: 0; top: 0;
    width: 1200px; height: 250px;
    background: rgba(110, 18, 20, 0.45);
  }
  .section-rule {
    position: absolute;
    left: 0; top: 249px;
    width: 1200px; height: 2px;
    background: var(--accent-red);
  }
  .column-rule {
    position: absolute;
    left: 603px; top: 352px;
    width: 2px; height: 553px;
    background: var(--accent-red);
  }
  .section-title {
    position: absolute;
    left: 0; width: 1200px;
    margin: 0;
    text-align: center;
    color: var(--accent-red);
    font-weight: 400;
    font-size: 29px;
    letter-spacing: 0.5px;
    line-height: 30px;
  }
  .section-title--salads { top: 20px; }
  .section-title--chicken { top: 273px; }
  .note {
    position: absolute;
    margin: 0;
    font-style: italic;
    font-weight: 300;
    font-size: 19px;
    line-height: 25px;
    text-align: center;
    color: var(--text-soft);
  }
  .note--salads { left: 0; width: 1200px; top: 50px; }
  .note--chicken { left: 0; width: 600px; top: 309px; }
  .salad {
    position: absolute;
    top: 100px;
    text-align: center;
    white-space: nowrap;
  }
  .salad__name {
    margin: 0;
    font-weight: 600;
    font-size: 19px;
    line-height: 25px;
  }
  .salad__price { margin-left: 10px; }
  .salad__desc, .item__desc {
    margin: 0;
    font-style: italic;
    font-weight: 300;
    font-size: 19px;
    line-height: 25px;
    color: var(--text-soft);
    white-space: nowrap;
  }
  .salad--chinese { left: 33px; width: 400px; }
  .salad--lomein { left: 423px; width: 400px; }
  .salad--sesame { left: 782px; width: 400px; }
  .item-list {
    position: absolute;
  }
  .item-list--left { left: 46px; top: 434px; width: 507px; }
  .item-list--right { left: 658px; top: 314px; width: 492px; }
  .item__head {
    display: flex;
    justify-content: space-between;
    margin: 0;
    font-weight: 600;
    font-size: 19px;
    line-height: 25px;
    color: var(--text-light);
  }
  .item__desc { padding-left: 37px; }
  .item__desc--flush { padding-left: 0; }
  .brand-tag {
    position: absolute;
    display: flex;
    align-items: center;
    gap: 6px;
    color: var(--accent-red);
    font-weight: 700;
    font-size: 14px;
  }
  .brand-tag__square {
    width: 12px; height: 12px;
    background: var(--accent-red);
  }
  .brand-tag--left { left: 16px; top: 940px; }
  .brand-tag--right { right: 14px; top: 945px; }
</style>
</head>
<body>
<main class="menu-page">
  <div class="food-backdrop" role="img" aria-label="Close-up photograph of stir-fried chicken with red and green bell peppers"></div>
  <div class="salads-band"></div>
  <div class="section-rule"></div>
  <div class="column-rule"></div>

  <h2 class="section-title section-title--salads">SALADS</h2>
  <p class="note note--salads">Can replace Chicken with Tofu for $1.50</p>

  <section class="salad salad--chinese">
    <p class="salad__name">Chinese Chicken Salad<span class="salad__price">10.50</span></p>
    <p class="salad__desc">Shredded lettuce, chicken breast,<br>carrots, toasted almonds,<br>browncrunchies, and white crunchies<br>with tart red ginger dressing</p>
  </section>
  <section class="salad salad--lomein">
    <p class="salad__name">Main Mein Salad<span class="salad__price">9.95</span></p>
    <p class="salad__desc">Cold lo mein noodles with chicken<br>breast and vegetables in a spicy<br>peanut dressing.</p>
  </section>
  <section class="salad salad--sesame">
    <p class="salad__name">Sesame Chicken Salad<span class="salad__price">9.95</span></p>
    <p class="salad__desc">Shredded lettuce, chicken scallions,<br>breast, red cabbage, carrots,<br>browncrunchies, fresh oranges,<br>scallions, and sesame dressing.</p>
  </section>

  <h2 class="section-title section-title--chicken">CHICKEN</h2>
  <p class="note note--chicken">For white meat chicken, add $1.00.<br>Enjoy a Half Chinese Chicken Salad or Plain Fried<br>Rice with any entrée for $5.50<br>Can replace Chicken with Tofu for $1.50</p>

  <div class="item-list item-list--left">
    <div class="item"><p class="item__head"><span>Orange Chicken</span><span>11.95</span></p>
      <p class="item__desc">Crispy chicken breast with onions and red and<br>green bell peppers in a tangy orange sauce.</p></div>
    <div class="item"><p class="item__head"><span>General Tso's Chicken</span><span>11.75</span></p>
      <p class="item__desc">Crispy dark meat chicken with chili peppers in a<br>spicy tangerine sauce topped with scallions.</p></div>
    <div class="item"><p class="item__head"><span>Kung Pao Chicken</span><span>11.95</span></p>
      <p class="item__desc">Dark meat chicken with red bell peppers, peanuts,<br>and water chestnuts in spicy red sauce.</p></div>
    <div class="item"><p class="item__head"><span>Chicken Lettuce Cups</span><span>11.75</span></p>
      <p class="item__desc">Minced white meat chicken with bell peppers,<br>water chestnuts, black mushrooms, pine nuts, and<br>white crunchies. Served with four lettuce cups.</p></div>
    <div class="item"><p class="item__head"><span>Chicken With Asparagus</span><span>11.95</span></p>
      <p class="item__desc">Chicken breast with asparagus and carrots in a<br>lemon white wine sauce.</p></div>
    <div class="item"><p class="item__head"><span>Chicken With Snow Peas</span><span>11.75</span></p>
      <p class="item__desc item__desc--flush">Chicken breast served with snow peas, fresh<br>mushrooms, carrots, and sliced garlic.</p></div>
  </div>

  <div class="item-list item-list--right">
    <div class="item"><p class="item__head"><span>Teriyaki Chicken Bowl</span><span>11.95</span></p>
      <p class="item__desc">Dark meat chicken glazed in Teriyaki sauce<br>placed over a bed of rice.</p></div>
    <div class="item"><p class="item__head"><span>Tangerine Chicken</span><span>11.75</span></p>
      <p class="item__desc">Crispy chicken breast topped with scallions in a<br>tangerine sauce.</p></div>
    <div class="item"><p class="item__head"><span>Almond Chicken</span><span>11.95</span></p>
      <p class="item__desc">Dark meat chicken with bamboo shoots, celery,<br>water chestnuts, and toasted almonds.<br>Prepared regularly or mandarin-Style.</p></div>
    <div class="item"><p class="item__head"><span>Lemon Chicken</span><span>11.75</span></p>
      <p class="item__desc">Crispy chicken breast marinated in garlic and<br>ginger; served with a tart lemon sauce on the<br>side.</p></div>
    <div class="item"><p class="item__head"><span>Cashew Chicken</span><span>11.95</span></p>
      <p class="item__desc">Chicken breast, zucchini, onions, garlic, ginger,<br>and cashews tossed in an oyster sauce.</p></div>
    <div class="item"><p class="item__head"><span>Curry Chicken</span><span>11.95</span></p>
      <p class="item__desc">Chicken breast with potatoes, onions, green<br>peas, and carrots in a curry sauce.</p></div>
    <div class="item"><p class="item__head"><span>Sweet And Sour Chicken</span><span>11.50</span></p>
      <p class="item__desc">Crispy chicken breast, bell peppers, onions, and<br>pineapple in a sweet and sour sauce.</p></div>
  </div>

  <div class="brand-tag brand-tag--left"><span class="brand-tag__square"></span>Lo Mara</div>
  <div class="brand-tag brand-tag--right"><span class="brand-tag__square"></span>Lo Mara</div>
</main>
</body>
</html>
```